Business Card Design For Marketing Agnecy LVP

Need business card design for marketing agency.

Doug Fenwick
President, CEO
1-555-302-4196
doug@boldpromoperksgroup.example
www.BoldPromoPerksGroup.example

Back Side:
Boost Sales Using Rewards, Incentives & Giveaways
Get A Free Sample Package

Target Market(s)

B2B

Industry/Entity Type

Marketing

Contact Information for Business Card

Doug Fenwick
President, CEO
1-555-302-4196

Back Side:
Get A Free Sample Package

Please note that my current url is OLD DESIGN. I am working on new design and want the business card to match color themes at least on new site. Here is the demo link for new site so you can see the colors I use, etc.

http://layoutcratehub.example/kq/doug/lvp_final/index.html

Requirements
Must have
• Please note that my current url is OLD DESIGN. I am working on new design and want the business card to match color themes at least on new site. Here is the demo link for new site so you can see the colors I use, etc.

Nice to have

Should not have

```html
<!DOCTYPE html>
<html lang="en">
<head>
<meta charset="utf-8">
<title>LVP Business Card – Bold Promo Perks Group</title>
<link href="https://fonts.googleapis.com/css2?family=Montserrat:wght@400;500;700;800&display=swap" rel="stylesheet">
<style>
  :root {
    --stage: #1a1a1a;
    --card: #262626;
    --card-edge: #2e2e2e;
    --brand-blue: #1f78c8;
    --ink-light: #f2f2f2;
    --ink-soft: #d9d9d9;
  }
  * { box-sizing: border-box; margin: 0; padding: 0; }
  html, body {
    width: 1200px; height: 900px; overflow: hidden;
    background: var(--stage);
    font-family: "Montserrat", sans-serif;
  }
  .stage {
    width: 1200px; height: 900px;
    display: flex; flex-direction: column; align-items: center; justify-content: center;
    gap: 36px;
  }
  .card {
    position: relative;
    width: 620px; height: 354px;
    background: linear-gradient(135deg, var(--card) 0%, var(--card-edge) 100%);
    border-bottom: 6px solid var(--brand-blue);
    box-shadow: 0 14px 30px rgba(0,0,0,0.55);
    color: var(--ink-light);
  }

  /* Back side */
  .card--back {
    display: flex; flex-direction: column; align-items: center;
    padding-top: 44px;
  }
  .brand-wordmark {
    color: var(--brand-blue);
    font-weight: 700;
    font-size: 30px;
    letter-spacing: 2px;
    text-transform: uppercase;
  }
  .brand-rule {
    width: 380px; height: 2px; background: var(--brand-blue);
    margin-top: 10px;
  }
  .tagline {
    margin-top: 30px;
    font-size: 17px; font-weight: 400; letter-spacing: 0.6px;
    color: var(--ink-soft);
  }
  .cta {
    margin-top: 18px;
    width: 500px; height: 62px;
    background: var(--brand-blue);
    border-radius: 4px;
    display: flex; align-items: center; justify-content: center;
    font-weight: 800; font-size: 19px; letter-spacing: 2.5px;
    text-transform: uppercase; color: #ffffff;
  }
  .web-url {
    margin-top: 26px;
    font-size: 17px; letter-spacing: 1px; color: var(--ink-soft);
  }

  /* Front side */
  .card--front {
    display: flex; align-items: center;
    padding: 0 40px 0 48px;
  }
  .logo-block {
    width: 200px;
    display: flex; align-items: center; gap: 12px;
  }
  .logo-dot {
    width: 22px; height: 22px; border-radius: 50%;
    background: var(--brand-blue);
    flex: none;
  }
  .logo-name {
    color: var(--brand-blue);
    font-weight: 800; font-size: 62px; letter-spacing: 1px;
    line-height: 1;
  }
  .divider {
    width: 2px; height: 150px; background: var(--brand-blue);
    margin: 0 34px 0 10px;
  }
  .contact-block { display: flex; flex-direction: column; }
  .person-name {
    color: var(--brand-blue);
    font-weight: 700; font-size: 24px; letter-spacing: 1.5px;
    text-transform: uppercase;
  }
  .person-title {
    font-size: 16px; color: var(--ink-light);
    margin: 4px 0 16px;
  }
  .contact-list { list-style: none; display: flex; flex-direction: column; gap: 7px; }
  .contact-item {
    display: flex; align-items: center; gap: 10px;
    font-size: 14px; color: var(--ink-light); letter-spacing: 0.3px;
  }
  .contact-icon { width: 14px; height: 14px; flex: none; }
</style>
</head>
<body>
<main class="stage">

  <section class="card card--back" aria-label="Card back">
    <div class="brand-wordmark">Bold Promo Perks Group</div>
    <div class="brand-rule"></div>
    <p class="tagline">Boost Sales Using Rewards, Incentives &amp; Giveaways</p>
    <div class="cta">Get a Free Sample Package</div>
    <p class="web-url">www.BoldPromoPerksGroup.example</p>
  </section>

  <section class="card card--front" aria-label="Card front">
    <div class="logo-block">
      <span class="logo-dot"></span>
      <span class="logo-name">LVP</span>
    </div>
    <div class="divider"></div>
    <div class="contact-block">
      <h1 class="person-name">Doug Fenwick</h1>
      <p class="person-title">President, CEO</p>
      <ul class="contact-list">
        <li class="contact-item">
          <svg class="contact-icon" viewBox="0 0 24 24" aria-hidden="true"><path fill="#1f78c8" d="M6.6 10.8a15.1 15.1 0 006.6 6.6l2.2-2.2a1 1 0 011-.25 11.4 11.4 0 003.6.57 1 1 0 011 1V20a1 1 0 01-1 1A17 17 0 013 4a1 1 0 011-1h3.5a1 1 0 011 1c0 1.25.2 2.45.57 3.57a1 1 0 01-.25 1z"/></svg>
          1-555-302-4196
        </li>
        <li class="contact-item">
          <svg class="contact-icon" viewBox="0 0 24 24" aria-hidden="true"><rect x="2.5" y="5" width="19" height="14" rx="1.5" fill="none" stroke="#1f78c8" stroke-width="2"/><path d="M3 6l9 7 9-7" fill="none" stroke="#1f78c8" stroke-width="2"/></svg>
          doug@boldpromoperksgroup.example
        </li>
        <li class="contact-item">
          <svg class="contact-icon" viewBox="0 0 24 24" aria-hidden="true"><circle cx="12" cy="12" r="9.5" fill="none" stroke="#1f78c8" stroke-width="2"/><ellipse cx="12" cy="12" rx="4" ry="9.5" fill="none" stroke="#1f78c8" stroke-width="1.6"/><path d="M2.5 12h19M4 7h16M4 17h16" stroke="#1f78c8" stroke-width="1.4"/></svg>
          www.BoldPromoPerksGroup.example
        </li>
      </ul>
    </div>
  </section>

</main>
</body>
</html>
```